New Business Card for our Indoor Golf Training Facility

We are looking for designs for a new business card for our indoor golf training facility. Attached is our logo, our logo with our slogan, and here is our elevator pitch (What makes us different from the others) not sure if all the info will fit on one card, maybe you can condense the elevator pitch? here is the info

Elevator Pitch
We work with serious golfers and those that want to be serious golfers…
to make you better, faster, at all phases of the game…
We use the same state-of-the-art technology as professional golfers…
which produces data sets that shows your improvement in real time.
Our facility is available 24/7 to our members, which allows you to improve on your time.

our website: www.birchpinlinks.com

Target Market(s)

Golfers

Font styles to use
Serif
Sans Serif

Colors
ec1f27
f59195
fbd4d5
919191
d3d3d3
1b1b1b

Requirements
Must have
• our logo or our logo with the slogan, elevator pitch (can be condensed or shortened)

```html
<!DOCTYPE html>
<html lang="en">
<head>
<meta charset="utf-8">
<title>Birch Pin Links – Business Card</title>
<link rel="stylesheet" href="https://fonts.googleapis.com/css2?family=Open+Sans:wght@400;600;700&display=swap">
<style>
  :root {
    --red: #ec1f27;
    --grey: #919191;
    --grey-light: #d3d3d3;
    --card: #141414;
    --card-edge: #1b1b1b;
    --page: #e9e7e4;
    --white: #f2f2f2;
  }
  * { box-sizing: border-box; margin: 0; padding: 0; }
  html, body { width: 1200px; height: 844px; overflow: hidden; }
  body {
    background: var(--page);
    font-family: "Open Sans", Arial, sans-serif;
    display: flex;
    align-items: center;
    justify-content: center;
    gap: 60px;
  }
  .card {
    width: 525px;
    height: 300px;
    background: radial-gradient(ellipse at 40% 40%, var(--card-edge), var(--card) 75%);
    box-shadow: 0 6px 18px rgba(0,0,0,.25);
    position: relative;
    color: var(--white);
    overflow: hidden;
  }

  /* Front */
  .card-front { display: flex; }
  .brand-mark {
    width: 265px;
    display: flex;
    align-items: center;
    justify-content: center;
    padding-top: 40px;
  }
  .brand-mark .brand-name {
    color: var(--red);
    font-weight: 600;
    font-size: 26px;
    white-space: nowrap;
  }
  .contact {
    flex: 1;
    border-left: 1px solid #2a2a2a;
    margin: 28px 0 60px;
    padding: 4px 0 0 16px;
    font-size: 15px;
    line-height: 1.3;
    color: var(--grey-light);
  }
  .contact .person-name { color: var(--red); font-size: 17px; font-weight: 600; }
  .contact .person-role { margin-bottom: 12px; }
  .contact .line { display: flex; align-items: center; gap: 5px; }
  .contact .line svg { width: 12px; height: 12px; flex: none; }
  .contact .address { margin-top: 12px; }

  /* Back */
  .card-back {
    padding: 24px 20px;
    text-align: center;
  }
  .brand-title {
    font-size: 34px;
    font-weight: 700;
    color: var(--grey-light);
    line-height: 1.15;
  }
  .tagline { font-size: 13px; color: var(--grey); margin-top: 2px; }
  .pitch-title { color: var(--red); font-weight: 700; font-size: 17px; margin: 8px 0; }
  .pitch { font-size: 12.5px; line-height: 1.42; color: var(--white); }
  .pitch a { color: var(--red); text-decoration: none; }
</style>
</head>
<body>
  <section class="card card-front">
    <div class="brand-mark">
      <div class="brand-name">Birch Pin Links</div>
    </div>
    <div class="contact">
      <div class="person-name">Marcus Hale</div>
      <div class="person-role">Managing Director</div>
      <div class="line">
        <svg viewBox="0 0 12 12"><circle cx="6" cy="6" r="5" fill="none" stroke="#ec1f27" stroke-width="1.3"/><path d="M4 3.5l1 1.5-.6.7a4 4 0 0 0 1.9 1.9l.7-.6 1.5 1-.7 1C5.5 8.6 3.4 6.5 3 4.2z" fill="#ec1f27"/></svg>
        555-018-2734
      </div>
      <div class="line">
        <svg viewBox="0 0 12 12"><circle cx="6" cy="6" r="5" fill="none" stroke="#ec1f27" stroke-width="1.3"/><circle cx="6" cy="6" r="2" fill="#ec1f27"/></svg>
        www.birchpinlinks.com
      </div>
      <div class="address">1480 Alder Ridge Rd. Unit B4<br>Fairmont, OH 45000</div>
    </div>
  </section>

  <section class="card card-back">
    <div class="brand-title">Birch Pin Links</div>
    <div class="tagline">Par Is Good. Better Is Better.</div>
    <div class="pitch-title">Elevator Pitch</div>
    <p class="pitch">
      We work with serious golfers and those that want to be serious golfers…<br>
      to make you better, faster, at all phases of the game…<br>
      We use the same state-of-the-art technology as professional golfers…<br>
      which produces data sets that shows your improvement in real time.<br>
      Our facility is available 24/7 to our members, which allows<br>
      you to improve on your time.<br>
      Visit <a href="#">www.birchpinlinks.com</a> for more details.
    </p>
  </section>
</body>
</html>
```